Property management company looking for modern card design

We at Blue Heron Partners provides property management services for its residential and commercial properties, with expertise in all categories of multifamily, industrial and office projects throughout California.

We need a business card design that is professional and modern designed business card. In our field, clients get hundreds of business cards, we would like our card to stand out.

Please avoid small print.

Target Market(s)

Professionals and high end clients

Industry/Entity Type

Financial Planning

Contact Information for Business Card

Company Name: Blue Heron Partners, Name, email, license #, phone number, website blueheronpartners.com

Font styles to use
Sans Serif

Requirements
Must have
• The card design needs to be adaptable because there is a possibly we will be expanding into different sectors other than real estate. The card design should be focused on financial planning and asset management.
Nice to have
• Modern and simple business card. Eye catching. Non-standard size/shaped cards would be great.
• blueheronpartners.com
Should not have
• Too many bright color or any pictures or shapes of real estate stuff.

```html
<!DOCTYPE html>
<html lang="en">
<head>
<meta charset="utf-8">
<title>Blue Heron Partners — Business Card</title>
<link rel="stylesheet" href="https://fonts.googleapis.com/css2?family=Open+Sans:wght@400;600&display=swap">
<style>
  :root {
    --page-bg: #e9e6e1;
    --card-black: #0b0b0c;
    --card-sheen: #1c1c1f;
    --coral: #e23a55;
    --coral-soft: #f06a80;
    --text-light: #f2f2f2;
    --text-muted: #a9a9ad;
  }
  * { box-sizing: border-box; margin: 0; padding: 0; }
  html, body { width: 1200px; height: 858px; overflow: hidden; }
  body {
    background: var(--page-bg);
    display: flex;
    align-items: center;
    justify-content: center;
    gap: 48px;
    font-family: "Open Sans", Arial, sans-serif;
  }
  .card {
    position: relative;
    width: 520px;
    height: 297px;
    background: linear-gradient(150deg, var(--card-sheen) 0%, var(--card-black) 55%);
    border-radius: 4px;
    box-shadow: 0 10px 28px rgba(0,0,0,.28);
    overflow: hidden;
  }

  /* Front: brand block + contact block */
  .brand-block {
    position: absolute;
    left: 0; top: 0;
    width: 290px; height: 100%;
    display: flex;
    flex-direction: column;
    align-items: center;
    justify-content: center;
  }
  .brand-name {
    font-family: "Open Sans", Arial, sans-serif;
    font-weight: 400;
    font-size: 28px;
    letter-spacing: 4px;
    color: var(--coral);
    white-space: nowrap;
  }
  .brand-url {
    margin-top: 10px;
    font-size: 14px;
    color: var(--text-muted);
    white-space: nowrap;
  }
  .divider {
    position: absolute;
    left: 290px; top: 28px;
    width: 1.5px; height: 241px;
    background: linear-gradient(to bottom, rgba(226,58,85,0) 0%, var(--coral) 50%, rgba(226,58,85,0) 100%);
  }
  .contact-block {
    position: absolute;
    left: 316px; top: 0;
    height: 100%;
    display: flex;
    flex-direction: column;
    justify-content: center;
  }
  .contact-name {
    font-size: 22px;
    color: var(--coral-soft);
    margin-bottom: 26px;
  }
  .contact-line {
    font-size: 16px;
    color: var(--text-light);
    line-height: 1.55;
  }
  .contact-license { margin-top: 14px; }

  /* Back: centred brand */
  .card-back {
    display: flex;
    align-items: center;
    justify-content: center;
  }
  .card-back .brand-name { font-size: 38px; letter-spacing: 6px; }
</style>
</head>
<body>
  <section class="card card-front" aria-label="Business card front">
    <div class="brand-block">
      <div class="brand-name">BLUE HERON</div>
      <div class="brand-url">www.blueheronpartners.com</div>
    </div>
    <div class="divider" aria-hidden="true"></div>
    <div class="contact-block">
      <div class="contact-name">Nora Whitfield</div>
      <div class="contact-line">555-014-2870</div>
      <div class="contact-line">nora@heron.com</div>
      <div class="contact-line contact-license">Lic : 20480317</div>
    </div>
  </section>

  <section class="card card-back" aria-label="Business card back">
    <div class="brand-name">BLUE HERON</div>
  </section>
</body>
</html>
```